Growing Plumbing company requires signage for vans/trucks plus letterhead and business cards

Pelkey's Plumbing and Heating (see www.pelkeysnf.ca) is a well established plumbing and heating company that has been servicing the new construction, renovation and plumbing maintenance needs of residential and commercial clients for over 40 years. It operates in St. John's, Newfoundland and Labrador, Canada..

The company is now expanding into a new line of business (electrical contracting) and requires a slight modification to its existing logo. The change is from "Pelkey's Plumbing and Heating" to "Pelkey's Plumbing and Electrical". An existing raw data file is provided to allow for this slight change. NO OTHER CHANGE TO THE LOGO IS REQUIRED.

As a result of this logo change, the company would like to create a new corporate identity package that includes the following:

- Signage for company vans (sample provided with new suggestions requested)

- Signage for company trucks (simple sign on driver and passenger doors and on tailgate) (no sample exists).

- Corporate letter head (sample provided with new suggestions requested)

- Business cards (sample provided with new suggestions requested)
Updates

Hello all, 

To clarify: work on the corporate logo only requires the word change from "Heating" to "Electric". No other changes are requested on the logo. ie no changes to "D", etc. 

As a result of this slight logo change, we are also requesting suggestions that could be made to existing corporate signage, letterhead, etc. 

Thanks, 

The Pelkey's Team. 

The exact font files to be used have been uploaded.

To clarify on corporate name: 

It is to be "Pelkey's Plumbing and Electrical"   (Not Heating or Electric)

The Pelkey's Team

Industry/Entity Type

Residential

Logo Text

Pelkey's Plumbing and Electrical

Requirements
Must have
• For van and truck signage, we want something that is "clean". Phone number, website, and logo must be included.

For logo, except for change from "heating" to "electrical" no other changes are requested.

For the logo change, we will require logo to be provided for all reproduction requirements including vertical (stacked) and horizontal treatments; black & white / colour / reverse; file formats including vector (designer use) and jpeg/pdf/gif, etc. (user use); variety of sizes in all files (i.e. small, medium and large).
Nice to have
• An idea would be to have the business cards, signage and letterhead use the grey bars in the "D" of the logo as a background or to the side.

```html
<!DOCTYPE html>
<html lang="en">
<head>
<meta charset="utf-8">
<title>Pelkey's Plumbing and Electrical – Business Card</title>
<link rel="stylesheet" href="https://fonts.googleapis.com/css2?family=Roboto:wght@300;400;700;900&display=swap">
<style>
  :root {
    --navy: #0f3b6c;
    --navy-deep: #0a2f58;
    --steel: #6b6f75;
    --card-white: #ececec;
    --ink: #5b5e63;
    --logo-light: #dfe3e8;
    --backdrop: #d9d6d1;
  }
  * { margin: 0; padding: 0; box-sizing: border-box; }
  html, body {
    width: 1200px; height: 900px; overflow: hidden;
    background: var(--backdrop);
    font-family: "Roboto", Arial, sans-serif;
  }
  .canvas {
    position: relative; width: 1200px; height: 900px;
  }
  .card {
    position: absolute; left: 337px;
    width: 525px; height: 300px;
    overflow: hidden;
    box-shadow: 0 6px 18px rgba(0,0,0,.18);
  }
  .card--front {
    top: 110px;
    background: linear-gradient(160deg, var(--navy) 0%, var(--navy-deep) 100%);
    display: flex; align-items: center; justify-content: center;
  }
  .card--back { top: 490px; background: var(--card-white); }

  .wordmark { text-align: left; font-weight: 900; line-height: 1; }
  .wordmark__name { display: block; font-size: 46px; letter-spacing: .5px; }
  .wordmark__line { display: block; font-size: 13.5px; letter-spacing: 1.2px; text-transform: uppercase; margin-top: 6px; }
  .card--front .wordmark { color: var(--logo-light); }
  .card--back .wordmark {
    position: absolute; left: 42px; top: 112px; color: var(--navy);
  }
  .card--back .wordmark__name { font-size: 38px; }
  .card--back .wordmark__line { font-size: 11.5px; letter-spacing: 1px; }

  .divider {
    position: absolute; left: 290px; top: 40px;
    width: 1px; height: 196px; background: var(--navy);
  }
  .contact {
    position: absolute; left: 314px; top: 42px;
    color: var(--ink); font-size: 10.5px; line-height: 1.45;
  }
  .contact__name { font-size: 15px; font-weight: 300; letter-spacing: .6px; text-transform: uppercase; color: #6a6d72; }
  .contact__title { font-weight: 300; margin-bottom: 22px; }
  .contact__row { display: flex; gap: 12px; }
  .contact__label { width: 8px; }
  .contact__address { margin-top: 14px; }
  .contact__web { margin-top: 14px; color: var(--navy); font-weight: 700; }

  .band { position: absolute; bottom: 0; height: 18px; }
  .band--navy { left: 0; width: 362px; background: var(--navy); }
  .band--steel { left: 362px; right: 0; background: var(--steel); }
</style>
</head>
<body>
<main class="canvas">
  <section class="card card--front" aria-label="Business card front">
    <div class="wordmark">
      <span class="wordmark__name">Pelkey's</span>
      <span class="wordmark__line">Plumbing and Electrical</span>
    </div>
  </section>

  <section class="card card--back" aria-label="Business card back">
    <div class="wordmark">
      <span class="wordmark__name">Pelkey's</span>
      <span class="wordmark__line">Plumbing and Electrical</span>
    </div>
    <div class="divider"></div>
    <div class="contact">
      <div class="contact__name">Marla Quinlan</div>
      <div class="contact__title">Director</div>
      <div class="contact__row"><span class="contact__label">T</span><span>709.555.0142</span></div>
      <div class="contact__row"><span class="contact__label">E</span><span>info@pelkeysnf.ca</span></div>
      <div class="contact__address">48 Harbour View Rd<br>CBS NL, A1X 2K5</div>
      <div class="contact__web">www.pelkeysnf.ca</div>
    </div>
    <div class="band band--navy"></div>
    <div class="band band--steel"></div>
  </section>
</main>
</body>
</html>
```